Top Pour Web site design

The aim of Top Pour is to provide an online service which allows customers to pre-order drinks and gain incentives such as fast entry, special offers (drinks, entry fees), as well as allowing customers to compare drinking establishments based upon costs and ratings.

what is required is the design of the pages stated below completed to the specifications.

Target Market(s)

The target market of Top Pour is men and women between the ages of 18 to 26 mainly. Within the age range of 18 to 26 the more specific target groups

Industry/Entity Type

Online

Requirements
Must have
• What is required to be designed

Website to be viewable on different systems e.g desktop, laptop and for mobile devices a mobile friendly page

Home page

Logo
Company name
Log in
Sign up
Help
Social media links, Follow us link

Bar, pub, club search function
Search by postcode, establishment type, distance

Pictorial instructions of how to use the site like ( quick dine). The stages are 1) select location 2) build order and pay 3) pick up from bar

Pre load results of establishments

Drinking establishment sign up

Map showing search results

List of results

My basket window which shows your order

Pop out box for customer sign up

Buttons for FAQ, general information, company information, Privacy policy ect at bottom of page

The home page is required to be Clear, simple, easy to use and stylish but not over the top with to much information which will confuse the customers. The preloaded results need to be obvious and where can be seen. The pictorial instructions should go below the preloaded results. Once the search criteria has been filled in and has been submitted the preloaded results and pictorial instructions will be removed and be replaced by the map and search results.

Drinking establishment personal page requires

Details of drinking establishment (name, address, contact, map)
list of drinks avliable
My basket
Special Offers
Gallery
Calendar
Reviews section at the bottom

When a person clicks on a drinking establishment page what that person should see when they open the page is company name logo
with a list of the drinks they offer and special offers. Tabs or buttons for gallery, establishment details, calender and special offers should be located along top or down the left. when they are clicked on they will replace the menu.

The colour scheme is based around the logo which is attached. We do not want any pink or overly bright colours which would not go with the logo.

A site which we like is this one
http://www.quick-dine.example.co.uk/
this site is perfect simple, clear but also good looking. If you need inspiration you should use this site as a starting point.
Should not have
• what should be avoided is a site which like this one http://platepoint.example.co.uk/~beta/?gclid=XQMWpLaRtnfGDsHYbTqeKZPLv

it is to complicated with bad font and colours. The site just feels cheesy and not classy. we like very little about this site

```html
<!DOCTYPE html>
<html lang="en">
<head>
<meta charset="utf-8">
<title>Top Pour – Order your round online</title>
<link href="https://fonts.googleapis.com/css2?family=Open+Sans:wght@400;600;700&family=Cabin+Sketch:wght@400;700&display=swap" rel="stylesheet">
<style>
:root{
  --navy:#2e3192;
  --ink:#1c1c6b;
  --text:#333;
  --grey:#555;
  --gold:#c8901a;
  --line:#dcdcdc;
  --paper:#fff;
  --footer-muted:#b9b9e0;
}
*{box-sizing:border-box;margin:0;padding:0}
html,body{width:1200px;height:1125px;overflow:hidden;background:#fff}
body{position:relative;font-family:"Open Sans",Arial,sans-serif;color:var(--text)}
.abs{position:absolute}

/* header */
.brand{left:185px;top:44px;display:flex;align-items:center;gap:10px}
.brand-mark{width:40px;height:40px;border-radius:50%;background:var(--navy)}
.brand-name{font-size:31px;font-weight:600;color:var(--navy)}
.social{display:flex;gap:4px}
.social span{width:22px;height:22px;border-radius:50%;background:var(--navy);display:block}
.social.top{left:912px;top:19px}
.cart{left:554px;top:65px;font-size:12px;color:var(--grey);display:flex;align-items:center;gap:4px}
.cart b{color:#1f5fd6}
.checkout{left:713px;top:60px;width:72px;height:24px;border:1px solid #aaa;background:linear-gradient(#f4f4f4,#d8d8d8);font-size:12.5px;color:#444;text-align:center;line-height:22px}
.account{left:825px;top:61px;font-size:14.5px;font-weight:600;color:#555}
.help{left:937px;top:59px;width:81px;height:24px;border:1px solid #c9c9c9;border-radius:8px;font-size:12px;color:var(--navy);text-align:center;line-height:22px;background:#fff;box-shadow:0 1px 2px rgba(0,0,0,.15)}

/* banner */
.banner{left:185px;top:127px;width:826px;height:146px;background:linear-gradient(90deg,#1d2a6e,#2f3f9d 40%,#2a3a8e 70%,#1d2a6e);overflow:hidden}
.banner-title{left:66px;top:10px;font-family:"Cabin Sketch",cursive;font-weight:700;font-size:38px;color:#fff}
.field{top:68px;height:32px;background:linear-gradient(#e9e9e9,#cfcfcf);border:1px solid #bbb;font-size:13.5px;color:#666;padding-left:9px;line-height:30px}
.field.select::after{content:"";position:absolute;right:9px;top:13px;border:4px solid transparent;border-top:5px solid #333}
.search-btn{left:598px;top:68px;width:157px;height:32px;background:linear-gradient(#5a5de0,#3a3cc0);border:1px solid #8a8cf0;color:#fff;font-weight:700;font-size:15.5px;display:flex;align-items:center;justify-content:center;gap:8px}

/* listings */
.section-title{left:185px;top:284px;font-family:"Cabin Sketch",cursive;font-weight:700;font-size:40px;color:#555}
.venue{width:262px;height:129px;border:1px solid var(--line);background:#fff;box-shadow:0 0 3px rgba(0,0,0,.08)}
.venue-photo{position:absolute;left:10px;top:13px;width:58px;height:58px;background:linear-gradient(#6a6470,#2d2a30);box-shadow:0 2px 3px rgba(0,0,0,.3)}
.venue-name{position:absolute;left:76px;top:7px;font-size:16.5px;font-weight:600;color:var(--ink);white-space:nowrap}
.venue-row{position:absolute;left:76px;font-size:12px;color:var(--text);display:flex}
.venue-row dt{width:93px;font-weight:600}
.venue-row dd{color:#444}
.cost{color:var(--gold);font-weight:700;letter-spacing:2px}
.mugs{display:inline-flex;gap:3px;vertical-align:middle}
.mugs i{width:10px;height:8px;border-radius:1px;background:#5356d8;display:block}
.mugs i.off{background:#c4c4c4}

/* how it works */
.how{left:0;top:643px;width:1200px;height:377px;background:linear-gradient(#fff,#d9d9d9)}
.how-title{left:0;top:664px;width:1200px;text-align:center;font-family:"Cabin Sketch",cursive;font-weight:700;font-size:40px;color:var(--navy)}
.step{width:264px;height:190px;background:var(--paper);box-shadow:0 8px 6px -4px rgba(0,0,0,.35)}
.step-tape{position:absolute;left:90px;top:-14px;width:98px;height:26px;background:#d3d3d3;opacity:.85}
.step-num{position:absolute;left:30px;top:12px;width:28px;height:28px;border-radius:50%;background:var(--navy);color:#fff;font-family:"Cabin Sketch",cursive;font-weight:700;font-size:20px;text-align:center;line-height:28px}
.step-art{position:absolute;left:68px;top:28px;width:134px;height:90px;border-radius:8px}
.step-label{position:absolute;left:0;width:100%;top:136px;text-align:center;font-family:"Cabin Sketch",cursive;font-size:21px;color:#444}
.chev{width:28px;height:40px}

/* footer */
.footer{left:0;top:1020px;width:1200px;height:105px;background:var(--navy)}
.footer-links{left:181px;top:1057px;font-size:13px;color:#fff}
.footer-links span{margin:0 4px}
.copyright{left:181px;top:1077px;font-size:13px;color:var(--footer-muted)}
.social.bottom{left:905px;top:1062px}
.social.bottom span{background:#fff}
</style>
</head>
<body>

<header>
  <div class="abs brand"><span class="brand-mark"></span><span class="brand-name">Top Pour</span></div>
  <div class="abs social top" aria-label="Follow us"><span></span><span></span><span></span><span></span></div>
  <div class="abs cart">
    <svg width="12" height="11" viewBox="0 0 12 11"><path d="M0 1h2l2 6h6l2-5H3" fill="none" stroke="#333" stroke-width="1.6"/><circle cx="5" cy="9.5" r="1.2" fill="#333"/><circle cx="9" cy="9.5" r="1.2" fill="#333"/></svg>
    items : <b>0</b> Subtotal : <b>£0.0</b>
  </div>
  <div class="abs checkout">Checkout</div>
  <div class="abs account">Log in . Sign up</div>
  <div class="abs help">NEED HELP</div>
</header>

<section class="abs banner" aria-label="Search establishments">
  <div class="abs" role="img" aria-label="Blurred bar backdrop with beer taps" style="inset:0;background:radial-gradient(ellipse at 30% 70%,rgba(120,140,230,.35),transparent 60%),radial-gradient(ellipse at 75% 40%,rgba(110,130,220,.3),transparent 60%)"></div>
  <div class="abs banner-title">Order your round online</div>
  <div class="abs field" style="left:70px;width:156px">Your Postcode</div>
  <div class="abs field select" style="left:238px;width:165px">Establishment Type</div>
  <div class="abs field select" style="left:414px;width:175px">Distance</div>
  <div class="abs search-btn">SEARCH NOW
    <svg width="16" height="16" viewBox="0 0 16 16"><circle cx="6.5" cy="6.5" r="4.5" fill="none" stroke="#fff" stroke-width="2"/><path d="M10 10l5 5" stroke="#fff" stroke-width="2.4"/></svg>
  </div>
</section>

<h2 class="abs section-title">Drinking establishment</h2>

<main>
  <article class="abs venue" style="left:185px;top:351px">
    <div class="venue-photo" role="img" aria-label="Pub front photo"></div>
    <h3 class="venue-name">The LANTERN</h3>
    <dl>
      <div class="venue-row" style="top:34px"><dt>Provides</dt><dd>: Food &amp; Drink</dd></div>
      <div class="venue-row" style="top:55px"><dt>Special offers</dt><dd>: 15% Off</dd></div>
      <div class="venue-row" style="top:76px"><dt>Cost</dt><dd>: <span class="cost">£££</span></dd></div>
      <div class="venue-row" style="top:97px"><dt>Rating</dt><dd>: <span class="mugs"><i></i><i></i><i></i><i></i><i class="off"></i></span></dd></div>
    </dl>
  </article>
  <article class="abs venue" style="left:468px;top:351px">
    <div class="venue-photo" role="img" aria-label="Pub building photo" style="background:linear-gradient(#b9c3cf,#8c8670 60%,#3a3030)"></div>
    <h3 class="venue-name">HARBOUR ARMS</h3>
    <dl>
      <div class="venue-row" style="top:34px"><dt>Provides</dt><dd>: Food &amp; Drink</dd></div>
      <div class="venue-row" style="top:55px"><dt>Special offers</dt><dd>: 20% Off</dd></div>
      <div class="venue-row" style="top:76px"><dt>Cost</dt><dd>: <span class="cost">££££</span></dd></div>
      <div class="venue-row" style="top:97px"><dt>Rating</dt><dd>: <span class="mugs"><i></i><i></i><i></i><i></i><i></i></span></dd></div>
    </dl>
  </article>
  <article class="abs venue" style="left:751px;top:351px">
    <div class="venue-photo" role="img" aria-label="Pub window photo" style="background:linear-gradient(#3a3a3a,#d8d4cc 50%,#2a2a2a)"></div>
    <h3 class="venue-name">The LANTERN</h3>
    <dl>
      <div class="venue-row" style="top:34px"><dt>Provides</dt><dd>: Food &amp; Drink</dd></div>
      <div class="venue-row" style="top:55px"><dt>Special offers</dt><dd>: 8% Off</dd></div>
      <div class="venue-row" style="top:76px"><dt>Cost</dt><dd>: <span class="cost">£</span></dd></div>
      <div class="venue-row" style="top:97px"><dt>Rating</dt><dd>: <span class="mugs"><i></i><i></i><i></i><i class="off"></i><i class="off"></i></span></dd></div>
    </dl>
  </article>
  <article class="abs venue" style="left:185px;top:501px">
    <div class="venue-photo" role="img" aria-label="Bar interior photo" style="background:linear-gradient(#6a3a4a,#2a1518)"></div>
    <h3 class="venue-name">BELL &amp; COMPASS</h3>
    <dl>
      <div class="venue-row" style="top:34px"><dt>Provides</dt><dd>: Food &amp; Drink</dd></div>
      <div class="venue-row" style="top:55px"><dt>Special offers</dt><dd>: 10% Off</dd></div>
      <div class="venue-row" style="top:76px"><dt>Cost</dt><dd>: <span class="cost">£££££</span></dd></div>
      <div class="venue-row" style="top:97px"><dt>Rating</dt><dd>: <span class="mugs"><i></i><i></i><i></i><i></i><i></i></span></dd></div>
    </dl>
  </article>
  <article class="abs venue" style="left:468px;top:501px">
    <div class="venue-photo" role="img" aria-label="Club night photo" style="background:radial-gradient(circle at 40% 30%,#e04a8a,#6a1a3a 60%,#2a0a18)"></div>
    <h3 class="venue-name" style="top:5px">FIDDLESTICK</h3>
    <dl>
      <div class="venue-row" style="top:32px"><dt>Provides</dt><dd>: Food &amp; Drink</dd></div>
      <div class="venue-row" style="top:53px"><dt>Special offers</dt><dd>: 12% Off</dd></div>
      <div class="venue-row" style="top:74px"><dt>Cost</dt><dd>: <span class="cost">£££</span></dd></div>
      <div class="venue-row" style="top:95px"><dt>Rating</dt><dd>: <span class="mugs"><i></i><i></i><i></i><i class="off"></i><i class="off"></i></span></dd></div>
    </dl>
  </article>
  <article class="abs venue" style="left:751px;top:501px">
    <div class="venue-photo" role="img" aria-label="Pub exterior photo" style="background:linear-gradient(#9aa2a8,#3a4048 55%,#1e2226)"></div>
    <h3 class="venue-name" style="top:5px">DUKE OF FERNLEY</h3>
    <dl>
      <div class="venue-row" style="top:32px"><dt>Provides</dt><dd>: Food &amp; Drink</dd></div>
      <div class="venue-row" style="top:53px"><dt>Special offers</dt><dd>: 18% Off</dd></div>
      <div class="venue-row" style="top:74px"><dt>Cost</dt><dd>: <span class="cost">£££££</span></dd></div>
      <div class="venue-row" style="top:95px"><dt>Rating</dt><dd>: <span class="mugs"><i></i><i></i><i></i><i></i><i class="off"></i></span></dd></div>
    </dl>
  </article>
</main>

<section aria-label="How it works">
  <div class="abs how"></div>
  <h2 class="abs how-title">How it Works</h2>

  <div class="abs step" style="left:177px;top:752px">
    <span class="step-tape"></span><span class="step-num">1</span>
    <div class="step-art" role="img" aria-label="Map with magnifying glass illustration" style="background:linear-gradient(135deg,#4a9a58,#8cc46a 60%,#4a8ac8)"></div>
    <p class="step-label">Select Location</p>
  </div>
  <svg class="abs chev" style="left:417px;top:827px" viewBox="0 0 28 40"><path d="M6 4l16 16-16 16" fill="none" stroke="#b7acb2" stroke-width="7"/></svg>

  <div class="abs step" style="left:464px;top:752px">
    <span class="step-tape"></span><span class="step-num">2</span>
    <div class="step-art" role="img" aria-label="Cash register illustration" style="background:linear-gradient(#e0c870,#b8c4d8 50%,#8e9ab8)"></div>
    <p class="step-label">build order and pay</p>
  </div>
  <svg class="abs chev" style="left:703px;top:824px" viewBox="0 0 28 40"><path d="M6 4l16 16-16 16" fill="none" stroke="#b7acb2" stroke-width="7"/></svg>

  <div class="abs step" style="left:753px;top:752px">
    <span class="step-tape"></span><span class="step-num">3</span>
    <div class="step-art" role="img" aria-label="Two glasses of red wine illustration" style="background:linear-gradient(#f2f2f2,#8a1a3a 45%,#d8d8d8 80%,#e8d040)"></div>
    <p class="step-label">pick up from bar</p>
  </div>
</section>

<footer>
  <div class="abs footer"></div>
  <nav class="abs footer-links">FAQ<span>|</span>general information<span>|</span>company information<span>|</span>Privacy policy</nav>
  <p class="abs copyright">Copyright © 2013 Top Pour. All rights reserved</p>
  <div class="abs social bottom" aria-label="Follow us"><span></span><span></span><span></span><span></span></div>
</footer>

</body>
</html>
```